Varelko App for Smart Devices IoT WiFi Electronic

Varelko is a siren manufacturer. This application is used for the company's products that have a Wi-Fi connection and an internet connection, which can be configured and activated remotely through this application. In addition, this application is used to activate the siren at specific times for the start and end of shifts in companies and schools. Users will be siren installers and IT or HR managers.
In addition to activating motorized sirens timers, some siren models have speakers and allow you to play TTS (text to speech) audio, audio recorded by the user on the phone and upload audio (mp3) with playlist programming with start and end times.
Application screens: home with dashboard (one dashboard for each category). Device categories: timers, speakers, motorized siren. Screen for requesting evaluation in the Play Store. Screen for registering the user profile. Screen for registering devices according to their category (timers, speakers, motorized siren). Screen for registering device groups. Screen for pairing the device on the client's Wi-Fi network. Screen for registering activation times. Screen for uploading MP3 audios. Screen for registering playlists with audio selection, start and end times. Screen for recording audio for later sending to the speakers. Screen for converting text to speech and sending to the speakers. It is important to have a time picker with the day of the week to program the activation times and playlist.

Target Market(s)

Schools, Companies and Stores.

Industry/Entity Type

IoT

Font styles to use
Sans Serif
Other font styles liked:
• roboto

Colors
FFC000
F8CF3A
FAE287
FDF2CF
FEFAEE

Requirements
Must have
• time picker with weekdays for timer programming feature.
Nice to have
• app review request screen on play store

```html
<!DOCTYPE html>
<html lang="en">
<head>
<meta charset="utf-8">
<title>Varelko – Siren App Screens</title>
<link rel="stylesheet" href="https://fonts.googleapis.com/css2?family=Inter:wght@400;500;600;700&display=swap">
<style>
:root{
  --amber:#FFC000;
  --amber-soft:#F8CF3A;
  --sand:#FAE287;
  --cream:#FDF2CF;
  --paper:#FEF7DF;
  --ivory:#FEFAEE;
  --white:#FFFFFF;
  --ink:#111111;
  --muted:#555555;
  --hint:#9A9A9A;
  --stage:#F3F3F3;
}
*{box-sizing:border-box;margin:0;padding:0}
html,body{width:1200px;height:559px;overflow:hidden}
body{background:var(--stage);font-family:"Inter",sans-serif;color:var(--ink);position:relative}
.phone{position:absolute;top:44px;width:243px;height:470px;border-radius:24px;background:var(--white);overflow:hidden}
.phone::before{content:"";position:absolute;left:0;top:0;right:0;height:147px;background:var(--amber)}
.status{position:absolute;top:6px;left:12px;right:12px;display:flex;justify-content:space-between;align-items:center;font-size:8px;font-weight:500}
.status svg{height:7px;margin-left:4px}
.appbar{position:absolute;top:30px;left:12px;right:10px;height:32px;display:flex;align-items:center;justify-content:space-between}
.brand{font-weight:700;font-size:26px;letter-spacing:-.5px;color:var(--ink)}
.appbar-icons{display:flex;gap:10px;align-items:center}
.appbar-icons svg{width:15px;height:15px}
.card{position:absolute;left:12px;right:12px;top:71px;bottom:0;background:var(--paper);border-radius:14px 14px 0 0}
.title{position:absolute;left:0;right:0;text-align:center;font-size:11px;font-weight:600}
.abs{position:absolute}
.tile{position:absolute;left:7px;right:7px;background:var(--white);border-radius:16px;box-shadow:inset 12px 0 0 var(--amber)}
.tile .txt{position:absolute;left:21px;top:50%;transform:translateY(-50%);line-height:1.55}
.t-main{font-size:8px;font-weight:500}
.t-main small{font-size:5.5px;font-weight:500}
.t-sub{font-size:7.4px;color:#333}
.t-note{font-size:6px;color:#333}
.tile .tools{position:absolute;right:10px;top:50%;transform:translateY(-50%);display:flex;flex-direction:column;gap:6px}
.tools svg{width:8px;height:8px}
.toggle{position:absolute;width:24px;height:12px;border-radius:6px;background:var(--amber)}
.toggle::after{content:"";position:absolute;left:2px;top:2px;width:8px;height:8px;border-radius:50%;background:var(--white)}
.section{position:absolute;left:7px;font-size:10px;font-weight:500;display:flex;align-items:center;gap:4px}
.section svg{width:10px;height:10px}
.status-note{position:absolute;left:7px;right:6px;top:427px;font-size:8.6px;line-height:15px;color:var(--muted)}
.label{position:absolute;left:7px;font-size:5.6px;color:#444}
.field{position:absolute;left:7px;right:7px;height:19px;background:var(--white);border-radius:10px;font-size:6.4px;color:var(--hint);padding-left:8px;display:flex;align-items:center}
.field svg{position:absolute;right:8px;width:8px;height:8px}
.week{position:absolute;top:232px;left:0;right:0;height:14px;font-size:7.6px}
.select{position:absolute;left:7px;right:7px;top:275px;font-size:6.4px}
.select div{height:19px;display:flex;align-items:center;padding-left:8px;position:relative}
.select .head{background:var(--white);border-radius:8px 8px 0 0}
.select .opt{background:var(--ivory);height:19px}
.select .active{background:var(--sand);height:16px}
.select .head svg{position:absolute;right:8px;width:7px;height:7px}
.btn{position:absolute;left:81px;width:57px;top:346px;height:24px;border-radius:12px;background:var(--amber);font-size:10px;font-weight:600;display:flex;align-items:center;justify-content:center}
.device{position:absolute;left:7px;right:7px;height:23px;background:var(--white);border-radius:12px;font-size:6.4px;color:var(--hint);padding-left:8px;display:flex;align-items:center}
.device .toggle{right:8px;top:5.5px}
.pair-text{position:absolute;left:0;right:0;top:22px;text-align:center;font-size:11px;font-weight:600;line-height:20px}
.pair-node{position:absolute;text-align:center;font-size:7px;font-weight:600;width:50px}
.pair-node svg{width:32px;height:32px;display:block;margin:0 auto 2px}
.pair-link{position:absolute;left:67px;width:84px;top:110px;border-top:1.4px dashed var(--amber)}
</style>
</head>
<body>
<svg width="0" height="0" style="position:absolute">
  <symbol id="i-wifi" viewBox="0 0 24 24"><path d="M12 21L1 8c6-5 16-5 22 0z" fill="#111"/><text x="12" y="15" font-size="8" font-weight="700" text-anchor="middle" fill="#FFC000" font-family="Inter,sans-serif">?</text></symbol>
  <symbol id="i-grid" viewBox="0 0 24 24"><rect x="2" y="3" width="7" height="7" rx="1"/><rect x="11" y="3" width="7" height="7" rx="1"/><rect x="2" y="12" width="7" height="7" rx="1"/><rect x="11" y="12" width="7" height="7" rx="1"/><path d="M19.5 17l2 2 2-2" stroke="#111" fill="none" stroke-width="1"/></symbol>
  <symbol id="i-user" viewBox="0 0 24 24"><circle cx="12" cy="12" r="10.5" fill="none" stroke="#111" stroke-width="2"/><circle cx="12" cy="9.5" r="3.8"/><path d="M5 18.5c2-3 4.5-4 7-4s5 1 7 4c-2 2-4.3 3-7 3s-5-1-7-3z"/></symbol>
  <symbol id="i-clock" viewBox="0 0 24 24"><circle cx="12" cy="12" r="9.5" fill="none" stroke="#444" stroke-width="2"/><path d="M12 7v5l-3 2" stroke="#444" stroke-width="2" fill="none"/></symbol>
  <symbol id="i-pen" viewBox="0 0 24 24"><path d="M3 21l1-5L16 4l4 4L8 20z" fill="#444"/></symbol>
  <symbol id="i-cal" viewBox="0 0 24 24"><rect x="3" y="5" width="18" height="16" rx="2" fill="none" stroke="#111" stroke-width="2"/><path d="M3 10h18M8 3v4M16 3v4M7 14h2M11 14h2M15 14h2M7 17h2M11 17h2" stroke="#111" stroke-width="2"/></symbol>
  <symbol id="i-check" viewBox="0 0 24 24"><circle cx="12" cy="12" r="10" fill="none" stroke="#111" stroke-width="2"/><path d="M7.5 12.5l3 3 6-6" stroke="#111" stroke-width="2" fill="none"/></symbol>
  <symbol id="i-upload" viewBox="0 0 24 24"><path d="M12 3l6 7h-4v6h-4v-6H6z M4 19h16v2H4z" fill="#111"/></symbol>
  <symbol id="i-chev" viewBox="0 0 24 24"><path d="M5 9l7 7 7-7" stroke="#111" stroke-width="3" fill="none"/></symbol>
  <symbol id="i-signal" viewBox="0 0 18 12"><rect x="0" y="8" width="3" height="4"/><rect x="5" y="5" width="3" height="7"/><rect x="10" y="2" width="3" height="10"/><rect x="15" y="0" width="3" height="12"/></symbol>
  <symbol id="i-wf" viewBox="0 0 16 12"><path d="M8 12l-2.5-3a3.5 3.5 0 0 1 5 0zM3 6.5a7 7 0 0 1 10 0l-1.3 1.5a5 5 0 0 0-7.4 0zM0.5 3.8a11 11 0 0 1 15 0l-1.3 1.5a9 9 0 0 0-12.4 0z"/></symbol>
  <symbol id="i-batt" viewBox="0 0 26 12"><rect x="1" y="1" width="21" height="10" rx="2.5" fill="none" stroke="#111"/><rect x="3" y="3" width="15" height="6" rx="1"/><rect x="23" y="4" width="2" height="4" rx="1"/></symbol>
</svg>

<!-- Screen 1: dashboard -->
<section class="phone" style="left:55px">
  <div class="status"><span>9:41</span><span><svg viewBox="0 0 18 12" width="10"><use href="#i-signal"/></svg><svg viewBox="0 0 16 12" width="10"><use href="#i-wf"/></svg><svg viewBox="0 0 26 12" width="13"><use href="#i-batt"/></svg></span></div>
  <header class="appbar"><span class="brand">Varelko</span><span class="appbar-icons"><svg><use href="#i-wifi"/></svg><svg><use href="#i-grid"/></svg><svg><use href="#i-user"/></svg></span></header>
  <main class="card">
    <h1 class="title" style="top:12px">Motorized sirens timers</h1>
    <div class="tile" style="top:35px;height:32px"><div class="txt"><div class="t-main">Shift Timing</div><div class="t-sub">Activate the device for shift timing</div></div><span class="toggle" style="right:14px;top:10px"></span></div>
    <h2 class="section" style="top:81px"><svg><use href="#i-cal"/></svg>Schedules</h2>
    <div class="tile" style="top:105px;height:42px"><div class="txt"><div class="t-main">9:00 AM to 1:00 PM <small>(Weekdays)</small></div><div class="t-sub">1st half session,&nbsp; Audio: text to speech</div><div class="t-note">The shift has be started, Have a nice day</div></div><div class="tools"><svg><use href="#i-clock"/></svg><svg><use href="#i-pen"/></svg></div></div>
    <div class="tile" style="top:157px;height:31px"><div class="txt"><div class="t-main">1:00 AM to 2:00 PM <small>(Weekdays)</small></div><div class="t-sub">Lunch Time</div></div><div class="tools"><svg><use href="#i-clock"/></svg><svg><use href="#i-pen"/></svg></div></div>
    <div class="tile" style="top:198px;height:31px"><div class="txt"><div class="t-main">4:00 AM to 4:20 PM <small>(Weekdays)</small></div><div class="t-sub">Coffee Break</div></div><div class="tools"><svg><use href="#i-clock"/></svg><svg><use href="#i-pen"/></svg></div></div>
    <div class="tile" style="top:239px;height:31px"><div class="txt"><div class="t-main">6:00 AM <small>(Weekdays)</small></div><div class="t-sub">Signing out Time</div></div><div class="tools"><svg><use href="#i-clock"/></svg><svg><use href="#i-pen"/></svg></div></div>
    <div class="tile" style="top:281px;height:31px"><div class="txt"><div class="t-main">9:00 AM to 12.00 PM <small>(Weekend)</small></div><div class="t-sub">Special session</div></div><div class="tools"><svg><use href="#i-clock"/></svg><svg><use href="#i-pen"/></svg></div></div>
    <h2 class="section" style="top:335px"><svg><use href="#i-check"/></svg>Status</h2>
    <p class="status-note" style="top:355px">Next Ring of siren is at 1:00 PM to 2:00 PM which is lunch time (siren alarm in 20 mins)</p>
  </main>
</section>

<!-- Screen 2: new schedule -->
<section class="phone" style="left:337px">
  <div class="status"><span>9:41</span><span><svg viewBox="0 0 18 12" width="10"><use href="#i-signal"/></svg><svg viewBox="0 0 16 12" width="10"><use href="#i-wf"/></svg><svg viewBox="0 0 26 12" width="13"><use href="#i-batt"/></svg></span></div>
  <header class="appbar"><span class="brand">Varelko</span><span class="appbar-icons"><svg><use href="#i-wifi"/></svg><svg><use href="#i-grid"/></svg><svg><use href="#i-user"/></svg></span></header>
  <main class="card">
    <h1 class="title" style="top:12px">Add the new schedules for siren</h1>
    <span class="label" style="top:38px">Title of Siren alarm</span>
    <div class="field" style="top:48px">Enter</div>
    <span class="label" style="top:77px">Start Time of Siren</span>
    <div class="field" style="top:88px">Time</div>
    <span class="label" style="top:116px">End Time of Siren</span>
    <div class="field" style="top:127px">Time</div>
    <div class="week" style="top:161px">
      <span class="abs" style="left:13px;top:-1px;font-size:10px;font-weight:600">Week</span>
      <span class="abs" style="left:88px;top:1px">Weekdays</span>
      <span class="toggle" style="left:137px;top:0"></span>
      <span class="abs" style="left:173px;top:1px">Weekend</span>
    </div>
    <span class="label" style="top:190px">Audio Format</span>
    <div class="select" style="top:204px">
      <div class="head">MP3 Audio<svg><use href="#i-chev"/></svg></div>
      <div class="opt">Text-to-Speech</div>
      <div class="active">Audio Recording</div>
    </div>
    <span class="label" style="top:274px">Choose audio from files</span>
    <span class="label" style="top:284px;font-size:6.4px;color:var(--ink)">MP3 Audio</span>
    <div class="field" style="top:307px;height:20px">Choose audio from files<svg><use href="#i-upload"/></svg></div>
    <div class="btn">Add</div>
  </main>
</section>

<!-- Screen 3: device list -->
<section class="phone" style="left:619px">
  <div class="status"><span>9:41</span><span><svg viewBox="0 0 18 12" width="10"><use href="#i-signal"/></svg><svg viewBox="0 0 16 12" width="10"><use href="#i-wf"/></svg><svg viewBox="0 0 26 12" width="13"><use href="#i-batt"/></svg></span></div>
  <header class="appbar"><span class="brand">Varelko</span><span class="appbar-icons"><svg><use href="#i-wifi"/></svg><svg><use href="#i-grid"/></svg><svg><use href="#i-user"/></svg></span></header>
  <main class="card">
    <h1 class="title" style="top:19px">Devices Available to connect</h1>
    <div class="device" style="top:45px">Xyz timer<span class="toggle"></span></div>
    <div class="device" style="top:77px">IT Siren abc<span class="toggle"></span></div>
    <div class="device" style="top:108px">Support team speaker<span class="toggle"></span></div>
  </main>
</section>

<!-- Screen 4: wi-fi pairing -->
<section class="phone" style="left:901px">
  <div class="status"><span>9:41</span><span><svg viewBox="0 0 18 12" width="10"><use href="#i-signal"/></svg><svg viewBox="0 0 16 12" width="10"><use href="#i-wf"/></svg><svg viewBox="0 0 26 12" width="13"><use href="#i-batt"/></svg></span></div>
  <header class="appbar"><span class="brand">Varelko</span><span class="appbar-icons"><svg><use href="#i-wifi"/></svg><svg><use href="#i-grid"/></svg><svg><use href="#i-user"/></svg></span></header>
  <main class="card">
    <p class="pair-text">You will be connecting to Xyz<br>timer to your account using<br>wi-fi pairing</p>
    <div class="pair-node" style="left:21px;top:94px"><svg><use href="#i-user"/></svg>abc</div>
    <div class="pair-link"></div>
    <div class="pair-node" style="left:147px;top:94px"><svg viewBox="0 0 24 24"><circle cx="12" cy="12" r="10" fill="none" stroke="#111" stroke-width="2"/><path d="M12 6.5V12l4 3.5" stroke="#111" stroke-width="2" fill="none"/></svg>Xyz timer</div>
  </main>
</section>
</body>
</html>
```